Flyer for the Lumen 2025 Conference

I am looking to produce a flyer for our upcoming conference, Lumen 2025. This is an annual conference that we plan to publicize on social media. The ideal designer will create a flyer that is eye-catching and effectively communicates the key information. Please see attached our logo, speaker photo, and flyer content.

Target Market(s)

All demographics

Industry/Entity Type

Christian

Font styles to use
Sans Serif

Requirements
Should not have
• Cross, church

```html
<!DOCTYPE html>
<html lang="en">
<head>
<meta charset="utf-8">
<title>Lumen 2025 Conference Flyer</title>
<link rel="stylesheet" href="https://fonts.googleapis.com/css2?family=Anton&family=Montserrat:wght@500;600;700;800&family=Great+Vibes&display=swap">
<style>
  :root {
    --mat: #cbcbcd;
    --ink-dark: #05060f;
    --navy: #14195a;
    --royal: #2b3aa3;
    --orange: #f7a21b;
    --amber: #fbb62b;
    --white: #ffffff;
    --badge: #f4f4f4;
    --badge-mark: #1b1d2a;
  }
  * { margin: 0; padding: 0; box-sizing: border-box; }
  html, body { width: 911px; height: 1200px; overflow: hidden; background: var(--mat); }
  .canvas { position: relative; width: 911px; height: 1200px; background: var(--mat); }
  .flyer {
    position: absolute; left: 91px; top: 85px; width: 728px; height: 1030px; overflow: hidden;
    background:
      radial-gradient(ellipse 70% 55% at 95% 8%, var(--royal) 0%, rgba(43,58,163,0.6) 40%, transparent 75%),
      linear-gradient(160deg, #0a0d24 0%, var(--navy) 45%, #101650 65%, var(--ink-dark) 100%);
    font-family: "Montserrat", sans-serif; color: var(--white);
  }
  .speaker-photo-faded {
    position: absolute; left: 478px; top: 120px; width: 250px; height: 720px;
    background: radial-gradient(ellipse 60% 45% at 45% 35%, rgba(40,52,140,0.9) 0%, rgba(25,32,100,0.6) 55%, transparent 100%);
  }
  .speaker-photo {
    position: absolute; left: 0; top: 198px; width: 441px; height: 832px;
    background:
      radial-gradient(ellipse 30% 14% at 45% 17%, #7a4f36 0%, rgba(122,79,54,0.4) 60%, transparent 100%),
      radial-gradient(ellipse 60% 55% at 40% 60%, #1f5fb0 0%, #17489a 45%, rgba(16,40,110,0.6) 75%, transparent 100%);
  }
  .bottom-fade {
    position: absolute; left: 0; bottom: 0; width: 100%; height: 220px;
    background: linear-gradient(to bottom, transparent, var(--ink-dark) 75%);
  }
  .label { color: var(--orange); font-weight: 800; font-size: 18px; line-height: 21px; }
  .topic, .speaker { position: absolute; top: 47px; font-weight: 600; font-size: 19px; line-height: 21px; }
  .topic { left: 39px; }
  .speaker { right: 35px; text-align: right; }
  .brand {
    position: absolute; left: 230px; top: 70px; width: 270px;
    display: flex; align-items: center; justify-content: center; gap: 10px;
    font-weight: 700; font-size: 40px; line-height: 48px; letter-spacing: 2px; color: var(--white);
  }
  .brand-dot { width: 18px; height: 18px; border-radius: 50%; background: var(--orange); }
  .headline { position: absolute; left: 0; top: 0; width: 728px; height: 580px; }
  .schedule { position: absolute; left: 174px; top: 580px; }
  .row { display: flex; gap: 6px; margin-bottom: 7px; height: 46px; }
  .date, .time {
    width: 188px; height: 46px; display: flex; align-items: center; justify-content: center;
    font-family: "Anton", sans-serif; font-size: 25px; letter-spacing: -0.3px;
  }
  .date { background: var(--amber); color: var(--ink-dark); }
  .time { border: 1.5px solid var(--amber); color: var(--white); }
  .app { position: absolute; left: 464px; top: 826px; }
  .app-lead { font-size: 14.5px; font-weight: 500; line-height: 18px; }
  .app-name { color: var(--orange); font-size: 21px; font-weight: 800; line-height: 24px; }
  .stores { display: flex; gap: 7px; margin-top: 9px; }
  .store-badge {
    width: 82px; height: 26px; background: var(--badge); border-radius: 4px;
    display: flex; align-items: center; padding-left: 8px;
  }
  .store-badge-mark { width: 12px; height: 12px; border-radius: 50%; background: var(--badge-mark); }
  .contacts { position: absolute; left: 464px; top: 928px; list-style: none; }
  .contacts li { display: flex; align-items: center; gap: 8px; height: 21px; font-size: 15px; font-weight: 500; }
  .contacts svg { width: 16px; height: 16px; }
  .location { position: absolute; left: 29px; top: 898px; }
  .location-script { font-family: "Great Vibes", cursive; color: var(--orange); font-size: 40px; line-height: 46px; }
  .venue { font-weight: 800; font-size: 15.5px; line-height: 20px; }
  .address { font-weight: 500; font-size: 15.5px; line-height: 20px; }
</style>
</head>
<body>
<div class="canvas">
  <section class="flyer">
    <div class="speaker-photo-faded" role="img" aria-label="Faded blue-toned portrait of the speaker"></div>
    <div class="speaker-photo" role="img" aria-label="Seated portrait of the speaker in a blue suit and grey turtleneck"></div>
    <div class="bottom-fade"></div>

    <div class="topic"><div class="label">TOPIC:</div>THE VOICE<br>OF THE LORD</div>
    <div class="speaker"><div class="label">SPEAKER:</div>PROPHET<br>SAMUEL OKORO</div>

    <div class="brand"><span class="brand-dot"></span>LUMINA</div>

    <svg class="headline" viewBox="0 0 728 580" aria-label="Lumen 2025 — A Prophetic Conference">
      <defs>
        <linearGradient id="fire" x1="0" y1="0" x2="1" y2="1">
          <stop offset="0" stop-color="#d2561c"/>
          <stop offset="0.5" stop-color="#e8871f"/>
          <stop offset="1" stop-color="#f4a825"/>
        </linearGradient>
      </defs>
      <text x="206" y="271" textLength="305" lengthAdjust="spacingAndGlyphs" font-family="Anton, sans-serif" font-size="120" fill="url(#fire)">LUMEN</text>
      <text x="207" y="429" textLength="314" lengthAdjust="spacingAndGlyphs" font-family="Anton, sans-serif" font-size="166" fill="#ffffff">2025</text>
      <text x="204" y="510" textLength="315" lengthAdjust="spacingAndGlyphs" font-family="Anton, sans-serif" font-size="70" fill="#fbb62b">A PROPHETIC</text>
      <text x="204" y="555" textLength="307" lengthAdjust="spacingAndGlyphs" font-family="Montserrat, sans-serif" font-weight="600" font-size="44" fill="#ffffff">CONFERENCE</text>
    </svg>

    <div class="schedule">
      <div class="row"><div class="date">DECEMBER 26TH</div><div class="time">6:30PM - 9:00PM</div></div>
      <div class="row"><div class="date">DECEMBER 27TH</div><div class="time">5:30PM - 8:00PM</div></div>
      <div class="row"><div class="date">DECEMBER 29TH</div><div class="time">4:30PM - 7:00PM</div></div>
    </div>

    <div class="app">
      <div class="app-lead">Download the</div>
      <div class="app-name">LUMINA APP</div>
      <div class="app-lead">to stay updated on the event</div>
      <div class="stores">
        <div class="store-badge" role="img" aria-label="App store badge"><span class="store-badge-mark"></span></div>
        <div class="store-badge" role="img" aria-label="App store badge"><span class="store-badge-mark"></span></div>
      </div>
    </div>

    <ul class="contacts">
      <li><svg viewBox="0 0 16 16"><circle cx="8" cy="8" r="8" fill="#f7a21b"/><rect x="5.5" y="3.5" width="5" height="9" rx="1" fill="none" stroke="#05060f" stroke-width="1.2"/></svg>207 555 0142</li>
      <li><svg viewBox="0 0 16 16"><circle cx="8" cy="8" r="8" fill="#f7a21b"/><rect x="4" y="5" width="8" height="6" fill="none" stroke="#05060f" stroke-width="1.2"/><path d="M4 5l4 3.5L12 5" fill="none" stroke="#05060f" stroke-width="1.2"/></svg>contact@lumina.org</li>
      <li><svg viewBox="0 0 16 16"><circle cx="8" cy="8" r="8" fill="#f7a21b"/><circle cx="8" cy="8" r="4.5" fill="none" stroke="#05060f" stroke-width="1.1"/><path d="M3.5 8h9M8 3.5c-2 2.5-2 6.5 0 9M8 3.5c2 2.5 2 6.5 0 9" fill="none" stroke="#05060f" stroke-width="1"/></svg>www.lumina.org</li>
    </ul>

    <div class="location">
      <div class="location-script">Location</div>
      <div class="venue">The Harborview Performing Arts Center</div>
      <div class="address">218 Linden Avenue Brookfield, Maine 04000</div>
    </div>
  </section>
</div>
</body>
</html>
```